Wordpress Theme for Medical Clinics

** Please view updated Sitemap2.pdf doc to clarify some confusion ***

This is a multiuser WordPress subscription site for medical clinics. Please see attachment for sitemap. Please do not include extra content like social media icons, search bars, or images. If you have questions, please ask for clarification.
The site contains the following pages and sub-pages:

1. Home
2. Our Clinic
2a. Our Clinic > Mission
2b. Our Clinic > Services
2c. Our Clinic > Clinic Policies
2d. Our Clinic > Schedules
3. Our Staff
3a. Our Staff > [Staff member page]
4. Resources
4a. Resources > Patient Health (index)
4b. Resources > Patient Health (index) > [post]
4c. Resources > Links
4d. Resources > Forms
5. Alerts
5a. Alerts > [Alert Page]
6. Contact Us

Includes the Following Pages, Subpages, and Content
1. Home
a. About Us
b. Our Staff
c. Bulletins
d. Accepting New Patients (shown as an alert widget)
e. Links
i. Physician Toolbox
ii. Book an Appointment
f. Clinic Policies
i. Show first 3 policies (e.g. Late Arrivals, Missed Appointments, Fees)
ii. Link to Clinic Policies page
g. Primary widget (displayed on all pages)
i. Hours of operation
ii. Contact Info
1. Tel
2. Fax
3. Email
4. Address
5. Get directions (link to Google Maps)
2. Our Clinic
a. Main Page
i. Clinic Name
ii. Overview
iii. Languages Spoken
iv. Secondary Navigation
1. Mission
2. Services
3. Clinic Policies
4. Schedules (see attachment)
b. Our Clinic > Mission
c. Our Clinic > Services
i. For each service include service TITLE and DESCRIPTION
d. Our Clinic > Clinic Policies
i. For each policy include policy TITLE and DESCRIPTION
ii. Include the following policies in mockup
1. Late arrivals
2. Missed appointments
3. Fees for missed appointments
4. Referrals and follow-ups
5. Services not covered by RDA
6. Information for LTF patients
7. Medical Legal Reports
e. Our Clinic > Schedules
3. Our Staff
a. Main Page
i. Display a list of staff members. Include NAME and DESIGNATION
b. Our Staff > [Staff Name]
i. Include NAME, PICTURE, DESIGNATION, and BIO
4. Resources
a. Resources > Patient Health
i. Main Page
1. Posts (ordered by date)
a. Title
b. Summary
2. Side Navigation
a. Post Categories
ii. Patient Health > [post title]
1. Title
2. Post Category
3. Date
4. Author
5. Summary
6. Body
b. Resources > Links
1. Secondary Navigation - Categories
a. Sample Categories:
i. Local Services
ii. RDA and Drug Coverage
iii. Mental Health Resources
2. Category page
a. Include the following links in the 'Local Services' category
i. Hypertension clinics
ii. Home Care services
iii. Vaccine Clinics
c. Resources > Forms
i. Display a table with form TITLE and CATEGORY
ii. Side Navigation
1. Form Categories
a. Use the following sample Categories
i. Referrals
ii. Insurance
iii. Intake
iv. Discharge
v. Waivers
5. Alerts
a. Main page
i. List of all Alert posts
1. Include post TITLE as a link to the post
ii. Side Navigation
1. Alerts Archive
a. shown as Month + Number of posts
iii. Alerts > [Alert page]
1. Include TITLE, DATE, AUTHOR, BODY
6. Contact Us
a. Map
b. Hours of operation
c. Address
d. Phone number
e. Fax number
e. Fax number
f. Map
g. Email

Design notes:
- fixed width
- responsive (need designs for mobile, tablet, and desktop)
- simple, dark font, white background
- use Font Awesome icons where needed
- user adds own logo

Target Market(s)

Medical Clinics

Industry/Entity Type

Medical

Number of Pages Required

5+ page

Font styles to use
Serif
Sans Serif

Requirements
Must have
• Please keep designs very simple.
• Examples:
• https://www.quolbin.com/install
• http://www.ventrohax.com/company/about-us
• http://brindlequota.org/
• http://www.trosk.com/
Should not have
• Minimal or no use of shadows and gradients

```html
<!DOCTYPE html>
<html lang="en">
<head>
<meta charset="utf-8">
<title>Harlow Clinics</title>
<link rel="stylesheet" href="https://fonts.googleapis.com/css2?family=Jost:wght@400;500;600&family=Open+Sans:wght@400;600;700&display=swap">
<style>
:root{
  --navy:#0f4c81;
  --menu:#263b50;
  --circle:#4d6e8f;
  --teal:#2b9ad0;
  --sky:#69c4ec;
  --yellow:#fcd34d;
  --green:#3aa84a;
  --red:#d9342b;
  --text:#3a3a3a;
  --muted:#5f7f95;
  --panel:#f4f5f6;
  --rule:#e5e7ea;
}
*{box-sizing:border-box;margin:0;padding:0}
html,body{width:710px;height:1200px;overflow:hidden;background:#fff}
body{position:relative;font-family:"Open Sans",Arial,sans-serif;color:var(--text)}
.abs{position:absolute}
h1,h2,h3,.heading{font-family:"Jost",Arial,sans-serif;color:var(--navy);font-weight:500}

/* header */
.brand{left:66px;top:20px;display:flex;align-items:center;gap:7px;font-family:"Jost",sans-serif;font-size:21px;font-weight:500;color:var(--navy)}
.brand-mark{width:17px;height:17px;background:#1fa6d8;border-radius:3px}
.contact{top:21px;font-size:6px;color:#666;line-height:1.9}
.contact strong{display:flex;align-items:center;gap:4px;font-size:6.5px;color:var(--navy)}
.contact span{padding-left:11px}
.contact.phone{left:274px}
.contact.hours{left:356px;padding-left:9px;border-left:1px solid #ddd}
.menu{left:521px;top:18px;width:123px;height:149px;background:var(--menu);border-radius:3px;z-index:3;color:#fff;padding:8px 10px}
.menu-head{display:flex;justify-content:space-between;align-items:center;font-size:8px;font-weight:600;margin-bottom:6px}
.menu ul{list-style:none}
.menu li{font-size:8px;font-weight:600;height:24.5px;display:flex;align-items:center;gap:10px}
.menu li::before{content:"›";font-size:7px;opacity:.8}

/* hero */
.hero{left:0;top:58px;width:710px;height:245px;background:linear-gradient(90deg,#b9a89a 0%,#e3d8cf 30%,#d6d3d0 55%,#f4f3f1 78%,#fbfbfa 100%)}
.hero-circle{left:469px;top:123px;width:158px;height:158px;border-radius:50%;background:var(--circle);color:#fff;text-align:center;padding-top:40px}
.hero-circle h2{color:#fff;font-size:18px;font-weight:500}
.hero-circle p{font-size:5.3px;line-height:1.65;width:100px;margin:3px auto 8px}
.btn{display:inline-block;font-size:5.6px;font-weight:700;text-transform:uppercase;color:#333;background:var(--yellow);border-radius:2px;padding:4px 8px}
.arrow{width:22px;height:22px;border-radius:50%;background:rgba(150,190,220,.75);top:164px}

/* new patients */
.patients-title{left:65px;top:314px;font-size:15px}
.status{left:66px;top:341px;width:54px;height:15px;border:1px solid #ddd;border-radius:8px;font-size:7px;display:flex;align-items:center;gap:4px;padding-left:5px}
.dot{width:7px;height:7px;border-radius:50%;background:var(--green);display:inline-block}
.legend{left:70px;top:370px;font-size:4.8px;color:#555;display:flex;gap:7px}
.legend .dot{width:4px;height:4px;margin-right:2px}
.patient{top:317px;display:flex;gap:7px}
.patient-photo{width:67px;height:58px;background:linear-gradient(135deg,#c9b8a8,#e6dcd4)}
.patient h3{font-size:8.5px;margin:14px 0 4px}
.patient p{font-size:6px;line-height:1.75;width:80px}

/* about */
.section-title{left:0;width:710px;text-align:center;font-size:14.5px}
.about{left:68px;top:441px;width:576px;text-align:center;font-size:5.6px;line-height:2.2}
.about p+p{margin-top:10px}

/* alerts */
.alerts-title{left:67px;top:545px;font-size:14px}
.pager{left:632px;top:550px;font-size:7px;color:#999}
.rule{left:66px;width:578px;height:1px;background:var(--rule)}
.alert{top:593px;display:flex;gap:10px;width:170px}
.date{flex:none;width:29px;height:29px;background:var(--green);color:#fff;font-size:5.8px;font-weight:700;text-align:center;line-height:1.2;padding-top:3px}
.alert strong{display:block;font-size:5.8px;color:var(--navy);line-height:2.1}
.alert span{display:block;font-size:5.6px;color:var(--muted);line-height:2.1;padding-left:2px}

/* staff */
.staff{top:750px;width:128px}
.staff small{display:block;font-size:7px;font-weight:700;color:var(--navy)}
.staff h3{font-size:11.5px;color:var(--teal);margin:1px 0}
.staff em{display:block;font-style:normal;font-size:6px;font-weight:700;color:var(--navy)}
.staff p{font-size:5.9px;line-height:1.72;margin:11px 0 8px}
.more{display:inline-block;width:40px;height:13px;line-height:13px;text-align:center;background:var(--sky);font-size:5.8px;color:#244}
.view-all{left:317px;top:910px;width:77px;height:16px;line-height:16px;text-align:center;padding:0}

/* toolbox */
.toolbox{left:66px;top:978px;width:577px;height:124px;background:var(--panel)}
.toolbox-photo{left:4px;top:0;width:190px;height:124px;background:linear-gradient(120deg,#e9ecee,#cfd9e0 55%,#4aa3c9 80%,#d9dfe3)}
.toolbox h2{left:207px;top:30px;font-size:17.5px}
.toolbox p{left:207px;top:57px;width:300px;font-size:5.9px;line-height:1.8}
.read-more{left:208px;top:88px;width:40px;height:12px;line-height:12px;font-size:5.8px;text-align:center;background:var(--sky)}

/* footer */
.footer{left:0;top:1136px;width:710px;height:64px;background:var(--panel);text-align:center;font-family:"Jost",sans-serif;font-weight:500;color:#222}
.footer nav{font-size:8.5px;margin-top:20px;word-spacing:2px}
.footer nav span{margin:0 6px}
.footer small{display:block;font-size:8px;margin-top:6px}
</style>
</head>
<body>

<header>
  <div class="abs brand"><span class="brand-mark"></span>Harlow Clinics</div>
  <div class="abs contact phone">
    <strong><svg width="6" height="6" viewBox="0 0 10 10"><path d="M2 0l2 3-1 1c1 2 2 3 3 3l1-1 3 2-1 2C4 10 0 6 0 1z" fill="#f0b400"/></svg>Telephone</strong>
    <span>+49 30 55501234</span>
  </div>
  <div class="abs contact hours">
    <strong><svg width="6" height="6" viewBox="0 0 10 10"><circle cx="5" cy="5" r="4.2" fill="none" stroke="#f0b400" stroke-width="1.4"/><path d="M5 2.5V5h2" stroke="#f0b400" stroke-width="1.2" fill="none"/></svg>Hours of Operation</strong>
    <span>Mon- Sat 8:30am to 5:00pm &nbsp;| &nbsp;Sun - Holiday</span>
  </div>
  <nav class="abs menu">
    <div class="menu-head">Menu
      <svg width="11" height="9" viewBox="0 0 11 9"><rect width="11" height="2" fill="#3ab4e6"/><rect y="3.5" width="11" height="2" fill="#3ab4e6"/><rect y="7" width="11" height="2" fill="#3ab4e6"/></svg>
    </div>
    <ul><li>Home</li><li>Clinic</li><li>Our Staff</li><li>Resources</li><li>Contact Us</li></ul>
  </nav>
</header>

<section class="abs hero" role="img" aria-label="Photo of a smiling young nurse with an older woman patient"></section>
<div class="abs hero-circle">
  <h2>Harlow Clinics</h2>
  <p>Lorem Ipsum is simply dummy text of the printing and typesetting industry. Lorem Ipsum has been the industry's standard dummy text ever</p>
  <span class="btn">Book an Appointment</span>
</div>
<svg class="abs arrow" style="left:35px" viewBox="0 0 22 22"><path d="M13 6l-5 5 5 5" fill="none" stroke="#fff" stroke-width="2"/></svg>
<svg class="abs arrow" style="left:651px" viewBox="0 0 22 22"><path d="M9 6l5 5-5 5" fill="none" stroke="#fff" stroke-width="2"/></svg>

<section>
  <h2 class="abs patients-title">New Patients</h2>
  <div class="abs status"><span class="dot"></span>Available</div>
  <div class="abs legend"><span><span class="dot"></span>Accepting</span><span><span class="dot" style="background:var(--red)"></span>Not Accepting</span></div>
  <div class="abs patient" style="left:170px"><div class="patient-photo" role="img" aria-label="Patient portrait"></div><div><h3>Patient 1</h3><p>Lorem Ipsum is simply dummy text of the printing</p></div></div>
  <div class="abs patient" style="left:326px"><div class="patient-photo" role="img" aria-label="Patient portrait"></div><div><h3>Patient 1</h3><p>Lorem Ipsum is simply dummy text of the printing</p></div></div>
  <div class="abs patient" style="left:485px"><div class="patient-photo" role="img" aria-label="Patient portrait"></div><div><h3>Patient 1</h3><p>Lorem Ipsum is simply dummy text of the printing</p></div></div>
</section>

<section>
  <h2 class="abs section-title" style="top:407px">About Us</h2>
  <div class="abs about">
    <p>Lorem Ipsum is simply dummy text of the printing and typesetting industry. Lorem Ipsum has been the industry's standard dummy text ever since the 1500s, when an unknown printer took a galley of type and scrambled it to make a type specimen book. It has survived not only five centuries, but also the leap into electronic typesetting, remaining essentially unchanged. It was popularised in the 1960s with the release of Quillmark sheets containing Lorem Ipsum passages, and more recently with desktop publishing software like Pagewright Studio including versions of Lorem Ipsum.</p>
    <p>Lorem Ipsum is simply dummy text of the printing and typesetting industry. Lorem Ipsum has been the industry's standard dummy text ever since the 1500s.</p>
  </div>
</section>

<section>
  <h2 class="abs alerts-title">Alerts/Bulletins</h2>
  <div class="abs pager">‹ ›</div>
  <div class="abs rule" style="top:575px"></div>
  <article class="abs alert" style="left:66px"><div class="date">June<br>6th<br>2015</div><div><strong>Lorem Ipsum is simply dummy text of the printing and typesetting industry.</strong><span>Lorem Ipsum has been the industry's standard dummy text ever since the 1500s</span></div></article>
  <article class="abs alert" style="left:263px"><div class="date">June<br>6th<br>2015</div><div><strong>Lorem Ipsum is simply dummy text of the printing and typesetting industry.</strong><span>Lorem Ipsum has been the industry's standard dummy text ever since the 1500s</span></div></article>
  <article class="abs alert" style="left:462px"><div class="date">June<br>6th<br>2015</div><div><strong>Lorem Ipsum is simply dummy text of the printing and typesetting industry.</strong><span>Lorem Ipsum has been the industry's standard dummy text ever since the 1500s</span></div></article>
</section>

<section>
  <h2 class="abs section-title" style="top:681px;font-size:17px">Staff</h2>
  <div class="abs rule" style="top:721px"></div>
  <article class="abs staff" style="left:66px"><small>Staff 1</small><h3>Daniel Okoro</h3><em>Physician</em><p>Lorem Ipsum is simply dummy text of the printing and typesetting industry. Lorem Ipsum has been the industry's standard dummy text ever since the 1500s, when an unknown printer took</p><span class="more">More</span></article>
  <article class="abs staff" style="left:214px"><small>Staff 1</small><h3>Daniel Okoro</h3><em>Physician</em><p>Lorem Ipsum is simply dummy text of the printing and typesetting industry. Lorem Ipsum has been the industry's standard dummy text ever since the 1500s, when an unknown printer took</p><span class="more">More</span></article>
  <article class="abs staff" style="left:363px"><small>Staff 1</small><h3>Daniel Okoro</h3><em>Physician</em><p>Lorem Ipsum is simply dummy text of the printing and typesetting industry. Lorem Ipsum has been the industry's standard dummy text ever since the 1500s, when an unknown printer took</p><span class="more">More</span></article>
  <article class="abs staff" style="left:510px"><small>Staff 1</small><h3>Daniel Okoro</h3><em>Physician</em><p>Lorem Ipsum is simply dummy text of the printing and typesetting industry. Lorem Ipsum has been the industry's standard dummy text ever since the 1500s, when an unknown printer took</p><span class="more">More</span></article>
  <span class="abs btn view-all">View All Staff</span>
</section>

<section class="abs toolbox">
  <div class="abs toolbox-photo" role="img" aria-label="Photo of a smiling physician in blue scrubs holding a tablet"></div>
  <h2 class="abs">Physician Toolbox</h2>
  <p class="abs">Lorem Ipsum is simply dummy text of the printing and typesetting industry. Lorem Ipsum has been the industry's standard dummy text ever since the 1500s, when an unknown printer took</p>
  <span class="abs read-more">Read More</span>
</section>

<footer class="abs footer">
  <nav>Home<span>|</span>Clinic<span>|</span>Our Staff<span>|</span>Resources<span>|</span>Contact Us</nav>
  <small>© 2015 Company Name , All Rights Reserved</small>
</footer>

</body>
</html>
```